Chai Tea Company needs a Tea Packaging Box Design

Tea Packaging
Dimensions of the Tea Packaging Box: Height 13 cm; Width 8.5 cm; Depth 7 cm
Individual Teabag Packet/ Sachet: Width 6.5 cm; Length 8.25 cm
We are looking for a new tea packaging design, for our tea business. The material of the box is cardboard. We are also looking for a design that will be on each individual tea bag sachet/packet that goes into the box. This design will be very similar to what you design for the tea packaging box.
Product Info:
Our tea company is called “Velmora Brew”. We sell two types of Chai Tea, once called “Velmora Gold” and one called “Velmora Meadow”. The Velmora Gold has caffeine, while the Velmora Meadow is Naturally Caffeine Free. The Velmora Gold has a black tea base, while the Velmora Meadow has a Rooibos tea base. We will need two tea packaging designs, one for each Chai Tea flavour. The designs for both the teas can be similar, but make sure that you can easily distinguish one from the other (example: make them have different colours or pictures). Both the chai teas, come from the same product line.
Tea Packaging Design:
We are looking for high end tea packaging. We produce high quality teas, and we would like to portray this in our tea packaging. Our teas are made with no artificial flavourings, natural flavourings, or preservatives, so we would also like a natural, organic, high quality look to our tea packaging. Our current logo is a llama. It would be great if you could make the current logo more polished and well made. If you feel that the llama is not well suited or you would like to design the llama differently, we are open to your creative ideas.
General Basic Info:
Keep in mind, we will have both English and French writing on the tea packaging. You do not need to worry about the French writing (we will do the translation), just make sure there is room for it. However, if you feel that you are capable and knowledgeable of incorporating both French and English language into the tea packaging that would be of great help and value.
Back of the Box:
- Will have ingredients and brewing instructions. Basic brewing instructions are: “Add hot water to teabag. Steep for 5-7 minutes, depending on strength preferred. Add milk and your choice of sweetener. Enjoy! See inside panel of box for more detailed instructions”. (The basic brewing instructions, can further be polished or written in a more creative or professional manner).
Front of the Box:
- Will have company name, type of tea, little description of the tea
- 18 teabags
- 54 g (1.9 OZ)
- Should state that this is a product of Alberta, Canada.
Side of the Box:
Any creative wording, slogan, or description about the tea, or whatever you feel would be good on the side of the box.
On the inside flap of the side of the box, there will be detailed instructions on how to brew the tea. These will be different from the simplified brewing instructions on the back of the box. I have attached the advanced brewing instructions as a file. These instructions can further be simplified or reduced to make it easier and cleaner for the consumers to read.
Individual Tea Sachets/ Packets
- These will have a matching look and design of the tea box packaging, except on a smaller scale. Each individual sachet will have the company name, type of tea, little description of the tea in the front of the sachet, while the back will contain the ingredients, and basic brewing instructions.
I have attached a few files, with the dimensions, ingredients, detailed brewing directions, and current logo of the business.
If you have any questions, about the design or packaging please let me know. The winning designer will be required to do a few additional tweaks to finalize the product. Thank you for your time and happy designing!

```html
<!DOCTYPE html>
<html lang="en">
<head>
<meta charset="utf-8">
<title>Velmora Brew — Tea Box Fronts</title>
<link rel="stylesheet" href="https://fonts.googleapis.com/css2?family=Cinzel:wght@400;500&family=Yellowtail&family=Tenor+Sans&display=swap">
<style>
  :root {
    --page-bg: #ffffff;
    --paper: #ecebe7;
    --gold-rule: #a08a55;
    --gold-number: #9a8450;
    --gold-band: #7a6535;
    --gold-title: #8ea6b1;
    --gold-text: #2c6275;
    --gold-figure: #9fb8c4;
    --meadow-band: #2a0a0a;
    --meadow-title: #6e1f1f;
    --meadow-text: #7a2424;
    --meadow-figure: #a8454a;
    --label-grey: #6f6a5e;
  }
  * { box-sizing: border-box; margin: 0; padding: 0; }
  html, body { width: 1200px; height: 1000px; overflow: hidden; background: var(--page-bg); }
  .canvas { position: relative; width: 1200px; height: 1000px; }

  .pack {
    position: absolute; top: 82px; width: 546px; height: 835px;
    background: var(--band);
  }
  .pack--gold { left: 27px; --band: var(--gold-band); --title: var(--gold-title); --text: var(--gold-text); --figure: var(--gold-figure); }
  .pack--meadow { left: 627px; --band: var(--meadow-band); --title: var(--meadow-title); --text: var(--meadow-text); --figure: var(--meadow-figure); }

  .panel {
    position: absolute; left: 71px; top: 0; width: 404px; height: 835px;
    background: var(--paper); text-align: center; overflow: hidden;
  }
  .caffeine {
    position: absolute; top: 38px; left: 0; right: 0;
    font: 400 12px/1 "Cinzel", serif; color: var(--label-grey);
    text-transform: uppercase;
  }
  .caffeine span { margin: 0 14px; }
  .flavour {
    position: absolute; top: 72px; left: 0; right: 0;
    font: 400 50px/1.1 "Yellowtail", cursive; color: var(--title);
    text-shadow: 1px 1px 0 rgba(0,0,0,.25); white-space: nowrap;
  }
  .description {
    position: absolute; top: 154px; left: 16px; right: 16px;
    font: 400 16.5px/18px "Cinzel", serif; color: var(--text);
    text-transform: uppercase;
  }
  .rule {
    position: absolute; top: 214px; left: 29px; right: 29px;
    height: 2px; background: var(--gold-rule);
  }
  .description--fr {
    position: absolute; top: 222px; left: 14px; right: 14px;
    font: 400 11px/15px "Cinzel", serif; color: var(--text);
    text-transform: uppercase;
  }
  .mascot {
    position: absolute; top: 303px; left: 87px; width: 260px; height: 272px;
    background: linear-gradient(180deg, var(--figure), var(--text));
    opacity: .75; border-radius: 4px;
  }
  .brand {
    position: absolute; top: 584px; left: 0; right: 0;
    font: 500 38px/1 "Cinzel", serif; color: var(--text);
    text-transform: uppercase;
  }
  .tagline {
    position: absolute; top: 636px; left: 0; right: 0;
    font: 400 14px/1 "Cinzel", serif; color: var(--label-grey);
  }
  .count {
    position: absolute; top: 682px; left: 0; right: 0;
    font: 400 50px/1 "Tenor Sans", sans-serif; color: var(--gold-number);
  }
  .unit {
    position: absolute; top: 743px; left: 0; right: 0;
    font: 400 20px/1 "Tenor Sans", sans-serif; color: var(--gold-number); letter-spacing: 1px;
  }
  .unit--fr {
    position: absolute; top: 768px; left: 0; right: 0;
    font: 400 13px/1 "Tenor Sans", sans-serif; color: var(--label-grey); letter-spacing: 1px;
  }
  .weight {
    position: absolute; top: 792px; left: 0; right: 0;
    font: 500 14px/1 "Cinzel", serif; color: var(--label-grey);
  }
</style>
</head>
<body>
<div class="canvas">

  <section class="pack pack--gold">
    <div class="panel">
      <p class="caffeine"><span>With Caffeine</span><span>Avec la caféine</span></p>
      <h1 class="flavour">Velmora Gold</h1>
      <p class="description">An exotic blend of black tea, cardamon, fennel, cloves, ginger and cinnamon</p>
      <div class="rule"></div>
      <p class="description--fr">Un mélange exotique de thé noir, cardamome, le fenouil, clous de girofle, le gingembre et la cannelle</p>
      <div class="mascot" role="img" aria-label="Llama silhouette illustration in pale blue"></div>
      <p class="brand">Velmora Brew</p>
      <p class="tagline">Fine Teas &amp; Blends</p>
      <p class="count">18</p>
      <p class="unit">TEA BAGS</p>
      <p class="unit--fr">SACHETS DE THÉ</p>
      <p class="weight">54 G (1.9 OZ)</p>
    </div>
  </section>

  <section class="pack pack--meadow">
    <div class="panel">
      <p class="caffeine"><span>Caffeine Free</span><span>Sans caféine</span></p>
      <h1 class="flavour">Velmora Meadow</h1>
      <p class="description">A rich blend of South African rooibos tea, cardamon, fennel, cloves, ginger and cinnamon</p>
      <div class="rule"></div>
      <p class="description--fr">Un riche mélange du thé rooibos d'Afrique du Sud, la cardamome, le fenouil, clous de girofle, le gingembre et la cannelle</p>
      <div class="mascot" role="img" aria-label="Llama silhouette illustration in deep red"></div>
      <p class="brand">Velmora Brew</p>
      <p class="tagline">Fine Teas &amp; Blends</p>
      <p class="count">18</p>
      <p class="unit">TEA BAGS</p>
      <p class="unit--fr">SACHETS DE THÉ</p>
      <p class="weight">54 G (1.9 OZ)</p>
    </div>
  </section>

</div>
</body>
</html>
```